Flyer for Texas Schools Training and Certification Program

We need a 8.5 X 5.5 two sided flyer. One side will focus on the exclusive Certification we offer Independent Campus Accredited Fiscal Steward (ICAFS) These certified officers are prepared to run a multi-million dollar charter school. The other side will focus on the training available to all Texas Charter Board Members, Superintendents and Business Office staff. We provide required training hours that meet the QVD compliance requirements as well as CPA and GOVIK continuing education credits (CEU). Training are in the areas of Leadership, Human Resources, Finance, Grant Management and Facility Operations. Colors should be in keeping with the website. www.ICAFSGUILD.org. The flyer should include both the ICAFS and NDFR logos.

Target Market(s)

Charter School Administrators, Board Members and Business Office staff

Industry/Entity Type

Training

Requirements
Must have
• Eye catching quick read, color scheme in line with our website www.icafsguild.org.
• Clear offerings of live webinars and on-line (available 24x7) trainings
• Clear offerings meet the State required training hours - ICAFS is a State approved provider). It must have a much more professional design then the pieces I have been using.
Nice to have
• Fun, picture, feel of life is easier less hectic with ICAFS.

```html
<!DOCTYPE html>
<html lang="en">
<head>
<meta charset="utf-8">
<title>ICAFS Trainings Flyer</title>
<link rel="stylesheet" href="https://fonts.googleapis.com/css2?family=Arimo:wght@400;700&family=Tinos:wght@700&display=swap">
<style>
  :root {
    --maroon: #8e1b1f;
    --red: #b3282d;
    --ink: #3a3a3a;
    --grey: #9a9a9a;
    --band: #e9e9e9;
    --paper: #ffffff;
  }
  * { box-sizing: border-box; margin: 0; padding: 0; }
  html, body { width: 779px; height: 1200px; overflow: hidden; background: var(--paper); }
  .flyer {
    position: relative;
    width: 779px;
    height: 1200px;
    padding: 0 28px;
    font-family: "Arimo", Arial, sans-serif;
    color: var(--ink);
    background: linear-gradient(180deg, #f2f2f2 0, var(--paper) 160px);
  }
  .masthead { height: 150px; position: relative; }
  .brand {
    position: absolute; left: 0; top: 24px;
    display: flex; align-items: center; gap: 12px;
  }
  .brand-name {
    font-family: "Tinos", Georgia, serif; font-weight: 700;
    font-size: 50px; color: var(--maroon); letter-spacing: 1px; line-height: 1;
  }
  .brand-sub {
    font-size: 11px; color: var(--grey); line-height: 1.3; width: 160px;
    text-transform: uppercase; letter-spacing: .5px;
  }
  .partner {
    position: absolute; left: 400px; top: 32px;
    display: flex; align-items: center; gap: 10px;
  }
  .partner-mark { width: 24px; height: 24px; border-radius: 50%; background: var(--maroon); }
  .partner-name {
    font-family: "Tinos", Georgia, serif; font-weight: 700; font-size: 26px; color: var(--maroon);
  }
  .books {
    position: absolute; right: 0; top: 90px; width: 220px; height: 280px;
    background: linear-gradient(160deg, #e7b93a 0%, #d94a2a 40%, #9cc23a 70%, #c0392b 100%);
    border-radius: 6px 0 0 6px; opacity: .9;
  }
  .section-title {
    display: flex; align-items: center; gap: 12px;
    font-family: "Tinos", Georgia, serif; font-weight: 700; color: var(--maroon);
    font-size: 30px; line-height: 1.15; white-space: nowrap;
  }
  .section-title::before {
    content: ""; width: 15px; height: 15px; background: var(--red); flex: none;
  }
  .section { position: relative; }
  .intro { width: 510px; }
  .intro p { margin-top: 8px; font-size: 17px; line-height: 1.42; }
  .open { margin-top: 22px; }
  .conquer { margin-top: 14px; }
  .conquer .section-title { align-items: flex-start; }
  .conquer .section-title::before { margin-top: 10px; }
  .free { margin-top: 22px; }
  .list { list-style: none; margin: 8px 0 0 44px; }
  .list li {
    position: relative; font-size: 17px; line-height: 27px; padding-left: 16px;
  }
  .list li::before {
    content: ""; position: absolute; left: 0; top: 11px; width: 6px; height: 6px; background: var(--red);
  }
  .free p { margin-top: 12px; font-size: 17px; line-height: 1.5; }
  .free strong { color: var(--maroon); }
  .footer {
    position: absolute; left: 0; bottom: 0; width: 100%; height: 50px;
    background: var(--band); display: flex; align-items: center; justify-content: flex-end;
    padding-right: 30px; font-size: 16px; font-weight: 700; color: var(--maroon); letter-spacing: 1px;
  }
</style>
</head>
<body>
<main class="flyer">
  <header class="masthead">
    <div class="brand">
      <span class="brand-name">ICAFS</span>
      <span class="brand-sub">Independent Campus Accredited Fiscal Steward</span>
    </div>
    <div class="partner">
      <span class="partner-mark"></span>
      <span class="partner-name">NDFR</span>
    </div>
  </header>

  <div class="books" role="img" aria-label="Illustration of a stack of colorful books with spines reading Strategy, Practice, Skills, Learn, Lead"></div>

  <section class="section intro">
    <h2 class="section-title">Trainings:</h2>
    <p>ICAFS trainings are open to anyone (Business Office Staff, Superintendent, Board Members) and may be taken in any order, at any time. Trainings include live webinars, online courses and live training days. Live trainings are combination of Boot Camp (Case Studies); Business Week (Charter Business Updates) and Documentation Workshops (Procedure Manuals and Systems).</p>
  </section>

  <section class="section open">
    <h2 class="section-title">TRAININGS – Open to Everyone:</h2>
    <ul class="list">
      <li>Live Monthly Webinars</li>
      <li>On-Line 24 X 7 Courses</li>
      <li>Live Trainings throughout Texas</li>
      <li>Boot Camp – Hands on Scenario Based – Putting Knowledge to Work</li>
      <li>Business Week – Updates From the Experts</li>
      <li>Documentation Workshop – Creating Procedure Manuals and Systems</li>
      <li>All courses earn QVD Commissioner Hours, CPA CPE, and ICAFS Hours</li>
    </ul>
  </section>

  <section class="section conquer">
    <h2 class="section-title">CONQUER COMPETENCIES-<br>REALIZE CONTINUOUS IMPROVEMENT:</h2>
    <ul class="list">
      <li>Courses Offered in All Areas</li>
      <li>Courses Offered for All Levels</li>
      <li>Just in Time Training – Timed with Compliance and Time of Year</li>
      <li>Tuesday TIP – Timely How to on Current Compliance Deadlines</li>
      <li>Resource Center – Charter Business Office Specific</li>
    </ul>
  </section>

  <section class="section free">
    <h2 class="section-title">FREE How-To and Reminders:</h2>
    <p><strong>Register at www.ICAFSGUILD.org</strong> and start receiving your weekly tip, and browse the variety of courses for yourself, your superintendent, board members or business office staff. All trainings are open to anyone, those pursuing certification or just expanding his or her professional development.</p>
  </section>

  <footer class="footer">www.icafsguild.org</footer>
</main>
</body>
</html>
```